New Business Card Design Project

I need a design for business cards, i am an electrical business called "Corvane Electrical and Communications" i need the cards to be double sided with the company logo on the back (attached) the front needs to say my company name, web site, email address, telephone number, and ABN number and electrical license number. I am open to different arrangements of the information but would like the background to be incorporating something electrical or something that looks smart. open to all additional ideas also.

The company colours are orange and grey see logo attached.

Business Name: Corvane Electrical and Communications
Website: corvaneelectricalandcomms.example.com.au
Email: brent@corvaneelectricalandcomms.example.com.au
Telephone(mobile): 0481209736
ABN: 71208349162
Lic No: 418273D

Target Market(s)

Business entities, Project Managers, Accounts, Clients

Industry/Entity Type

Electrician

Contact Information for Business Card

I need a design for business cards, i am an electrical business called "Corvane Electrical and Communications" i need the cards to be double sided with the company logo on the back (attached) the front needs to say my company name

Font styles to use
Serif
Sans Serif

Colors
f37122
5c5c5c

Requirements
Must have
• Must have the Logo on the back open to different ways of it being on the back but had in mind to keep it central but again open to other options
Nice to have
• A real modern cool background that is eye catching yet contemporary
Should not have
• No backgrounds of a light bulb or plug or anything like that

```html
<!DOCTYPE html>
<html lang="en">
<head>
<meta charset="utf-8">
<title>Corvane Electrical and Communications – Business Card</title>
<link rel="stylesheet" href="https://fonts.googleapis.com/css2?family=Exo+2:wght@600;700&family=Raleway:wght@400;500&display=swap">
<style>
  :root {
    --orange: #f7a81b;
    --orange-deep: #f37122;
    --grey: #5c5c5c;
    --grey-dark: #4a4a4a;
    --white: #ffffff;
    --text-light: #e9e9e9;
    --stage: #e4e2de;
  }
  * { box-sizing: border-box; margin: 0; padding: 0; }
  html, body {
    width: 1200px; height: 950px; overflow: hidden;
    background: var(--stage);
  }
  .stage {
    width: 1200px; height: 950px;
    display: flex; align-items: center; justify-content: center; gap: 60px;
  }
  .card {
    position: relative;
    width: 380px; height: 600px;
    border-radius: 26px;
    box-shadow: 0 14px 30px rgba(0,0,0,.22);
  }
  .card__frame {
    position: absolute; inset: 14px;
    border-radius: 18px;
    border: 2px solid;
  }
  /* Front */
  .card--front { background: linear-gradient(160deg, var(--grey) 0%, var(--grey-dark) 100%); }
  .card--front .card__frame { border-color: var(--orange); }
  .front {
    position: absolute; inset: 0;
    display: flex; flex-direction: column; align-items: center;
    padding-top: 62px; text-align: center;
  }
  .brand-name {
    font-family: "Exo 2", sans-serif; font-weight: 700;
    color: var(--white); font-size: 30px; line-height: 1.15;
    letter-spacing: 1px; text-transform: uppercase;
    width: 300px;
  }
  .person { margin-top: 48px; display: flex; flex-direction: column; align-items: center; }
  .person__icon { width: 18px; height: 18px; margin-bottom: 4px; }
  .person__name {
    font-family: "Exo 2", sans-serif; font-weight: 700;
    color: var(--orange); font-size: 26px; letter-spacing: .5px;
  }
  .person__role {
    font-family: "Exo 2", sans-serif; font-weight: 600;
    color: var(--white); font-size: 17px; margin-top: 2px;
  }
  .registration {
    margin-top: 26px;
    font-family: "Raleway", sans-serif; font-weight: 500;
    color: var(--text-light); font-size: 17px; line-height: 1.4;
    letter-spacing: .5px;
  }
  .contact {
    margin-top: 20px; list-style: none;
    display: flex; flex-direction: column; align-items: center; gap: 6px;
    font-family: "Raleway", sans-serif; font-weight: 500;
    color: var(--text-light);
  }
  .contact__item { display: flex; flex-direction: column; align-items: center; gap: 4px; }
  .contact__icon { width: 16px; height: 16px; }
  .contact__phone { font-size: 17px; letter-spacing: .5px; }
  .contact__small { font-size: 12px; }
  /* Back */
  .card--back { background: linear-gradient(160deg, #f9b020 0%, var(--orange) 60%, #f29e14 100%); }
  .card--back .card__frame { border-color: var(--white); }
  .back {
    position: absolute; inset: 0;
    display: flex; flex-direction: column; align-items: center; justify-content: center;
    text-align: center; gap: 18px;
  }
  .back .brand-name { font-size: 32px; }
  .back__web {
    font-family: "Raleway", sans-serif; font-weight: 500;
    color: var(--white); font-size: 13px;
  }
</style>
</head>
<body>
<main class="stage">
  <section class="card card--front" aria-label="Card front">
    <div class="card__frame"></div>
    <div class="front">
      <h1 class="brand-name">Corvane Electrical and Communications</h1>

      <div class="person">
        <svg class="person__icon" viewBox="0 0 18 18" aria-hidden="true">
          <circle cx="9" cy="5" r="4" fill="var(--orange)"/>
          <path d="M1 18c0-5 3.5-8 8-8s8 3 8 8z" fill="var(--orange)"/>
        </svg>
        <p class="person__name">Dale Harper</p>
        <p class="person__role">CEO/Founder</p>
      </div>

      <div class="registration">
        <p>ABN: 71208349162</p>
        <p>Lic No: 418273D</p>
      </div>

      <ul class="contact">
        <li class="contact__item">
          <svg class="contact__icon" viewBox="0 0 16 16" aria-hidden="true">
            <rect x="4" y="1" width="8" height="14" rx="1.5" fill="none" stroke="var(--orange)" stroke-width="1.6"/>
            <circle cx="8" cy="12.5" r=".9" fill="var(--orange)"/>
          </svg>
          <span class="contact__phone">0481209736</span>
        </li>
        <li class="contact__item">
          <svg class="contact__icon" viewBox="0 0 16 16" aria-hidden="true">
            <rect x="1" y="3" width="14" height="10" rx="1" fill="var(--orange)"/>
            <path d="M1.5 3.5 8 9l6.5-5.5" fill="none" stroke="var(--grey-dark)" stroke-width="1.2"/>
          </svg>
          <span class="contact__small">brent@corvaneelectricalandcomms.example.com.au</span>
        </li>
        <li class="contact__item">
          <svg class="contact__icon" viewBox="0 0 16 16" aria-hidden="true">
            <circle cx="8" cy="8" r="6.5" fill="none" stroke="var(--orange)" stroke-width="1.5"/>
            <ellipse cx="8" cy="8" rx="2.8" ry="6.5" fill="none" stroke="var(--orange)" stroke-width="1.2"/>
            <path d="M1.5 8h13" stroke="var(--orange)" stroke-width="1.2"/>
          </svg>
          <span class="contact__small">corvaneelectricalandcomms.example.com.au</span>
        </li>
      </ul>
    </div>
  </section>

  <section class="card card--back" aria-label="Card back">
    <div class="card__frame"></div>
    <div class="back">
      <p class="brand-name">Corvane Electrical and Communications</p>
      <p class="back__web">corvaneelectricalandcomms.example.com.au</p>
    </div>
  </section>
</main>
</body>
</html>
```